BRISKLY sparkling water needs new artwork! Based in Southern California

"Briskly" is a new sparkling water company based in Southern California that offers refreshing flavors (lime, cherry, & mango) with B vitamins and antioxidants.

We would like to see packaging designs for standard 12oz cans for each of the three flavors.
Our initial preference is to have individual artwork for each flavor.

Attached are examples of competitors' designs.
Updates

We are extending the deadline for the Thanksgiving Holiday. Thank you all for your contributions.

```html
<!DOCTYPE html>
<html lang="en">
<head>
<meta charset="utf-8">
<title>Briskly — Cherry Can Label</title>
<link rel="stylesheet" href="https://fonts.googleapis.com/css2?family=Fredoka:wght@700&display=swap">
<style>
  :root {
    --label-pink: #f4677b;
    --ink: #1d1d1b;
    --fold-line: #8e94c8;
    --fruit-tone: #d9576b;
  }
  html, body {
    margin: 0;
    padding: 0;
    overflow: hidden;
  }
  .can-label {
    position: relative;
    width: 1200px;
    height: 492px;
    background: var(--label-pink);
    overflow: hidden;
  }
  .fold-line {
    position: absolute;
    left: 17px;
    right: 0;
    top: 190px;
    height: 4px;
    background: repeating-linear-gradient(90deg, var(--fold-line) 0 28px, transparent 28px 40px);
  }
  .bubbles {
    position: absolute;
    inset: 0;
  }
  .bubbles circle {
    fill: none;
    stroke: var(--ink);
    stroke-width: 3.5;
  }
  .fruit-art {
    position: absolute;
    background: var(--fruit-tone);
    border-radius: 46% 46% 0 0;
  }
  .fruit-art--left {
    left: 13px;
    top: 360px;
    width: 155px;
    height: 132px;
  }
  .fruit-art--right {
    left: 836px;
    top: 382px;
    width: 164px;
    height: 110px;
  }
  .brand-name {
    position: absolute;
    left: 193px;
    width: 690px;
    top: 222px;
    margin: 0;
    text-align: center;
    font-family: "Fredoka", sans-serif;
    font-weight: 700;
    font-size: 172px;
    line-height: 1;
    letter-spacing: -2px;
    color: var(--ink);
  }
</style>
</head>
<body>
  <main class="can-label">
    <div class="fold-line" aria-hidden="true"></div>

    <svg class="bubbles" viewBox="0 0 1200 492" width="1200" height="492" aria-hidden="true">
      <circle cx="154" cy="321" r="13"/>
      <circle cx="948" cy="321" r="9"/>
      <circle cx="1000" cy="325" r="13"/>
      <circle cx="1086" cy="343" r="9"/>
      <circle cx="1036" cy="371" r="19"/>
      <circle cx="1118" cy="383" r="10"/>
      <circle cx="365" cy="455" r="14"/>
      <circle cx="658" cy="445" r="14"/>
      <circle cx="598" cy="461" r="9"/>
      <circle cx="546" cy="464" r="10"/>
      <circle cx="745" cy="468" r="14"/>
      <circle cx="1080" cy="454" r="9"/>
      <circle cx="1176" cy="443" r="14"/>
    </svg>

    <div class="fruit-art fruit-art--left" role="img" aria-label="Line illustration of cherries with a leaf"></div>
    <div class="fruit-art fruit-art--right" role="img" aria-label="Line illustration of cherries with a leaf"></div>

    <h1 class="brand-name">Briskly</h1>
  </main>
</body>
</html>
```